A start-up named "lumerova" - a clinical research organization needs a new PowerPoint design

We need a new PowerPoint Design (incl. business card and stationery design) for an early-stage start-up named "lumerova" seeking to build an ecosystem/ strategic partner alliances or consortium of committed and active collaborators to guide important components of the clinical trial.

Our ultimate goal is to avoid false neutrals – therapies that have not been and may never be evaluated in clinical trials due to the costs and/ or complexity.

The final design should highlight our patient-centric approach, innovative study design supported with the novel AI platform to make a stronger impact on patient lives.

Please see the attached brief for more details.
Updates

Requesting the proposals on color-coding, business-card designs, clinical research visuals, and icons as well as stationery design.

Target Market(s)

Pharma/ Biotech Executives
Medical Institutions
Clinical Trial Participants (Patients)

Colors
e34398

Requirements
Must have
• Use the Color Version of purple/ magenta logo

```html
<!DOCTYPE html>
<html lang="en">
<head>
<meta charset="utf-8">
<title>lumerova – Clinical Research Organization</title>
<link href="https://fonts.googleapis.com/css2?family=Montserrat:wght@600;700;800;900&family=Arimo:wght@400;600&display=swap" rel="stylesheet">
<style>
:root{
  --magenta:#d92a8a;
  --purple:#4a33c4;
  --violet:#6a2fc0;
  --ink:#222;
  --body:#777;
  --rule:#cfcfcf;
  --lavender:#b9aef0;
}
*{margin:0;padding:0;box-sizing:border-box}
html,body{width:1200px;height:5324px;overflow:hidden;background:#fff}
body{position:relative;font-family:"Arimo",Arial,sans-serif;color:var(--body)}
.abs{position:absolute}
.heading{font-family:"Montserrat",Arial,sans-serif;font-weight:800;color:var(--ink);text-align:center;width:100%;font-size:50px;letter-spacing:1px}
.underline{position:absolute;left:571px;width:58px;height:5px;background:var(--purple)}
.separator{position:absolute;left:0;width:1200px;height:6px;background:var(--rule)}

/* hero */
.hero{top:0;left:0;width:1200px;height:781px;background:linear-gradient(120deg,#d8278e 0%,#9a2cb4 50%,#4b37cc 100%)}
.brand{position:absolute;top:330px;left:0;width:1200px;display:flex;justify-content:center;align-items:center;gap:30px}
.brand-name{font-family:"Montserrat",Arial,sans-serif;font-weight:800;font-size:130px;color:#fff;letter-spacing:-3px}
.brand-square{width:60px;height:60px;background:#fff;border-radius:8px}

/* services */
.service{position:absolute;width:500px;height:130px}
.service-icon{position:absolute;left:0;top:0;width:116px;height:116px;border-radius:50%;display:flex;align-items:center;justify-content:center}
.service-icon::after{content:"";position:absolute;inset:6px;border:2px solid rgba(255,255,255,.55);border-radius:50%}
.service-icon.purple{background:var(--purple)}
.service-icon.magenta{background:var(--magenta)}
.service-title{position:absolute;left:148px;top:12px;font-family:"Montserrat",Arial,sans-serif;font-weight:600;font-size:23px;color:#333}
.service-text{position:absolute;left:150px;top:50px;width:372px;font-size:12.5px;line-height:23px;color:#888;text-align:justify}

/* clinical */
.lab-photo{top:1596px;left:0;width:605px;height:818px;background:linear-gradient(135deg,#dceaf6 0%,#9fc4e6 45%,#3f7fc4 100%)}
.cro-title{top:1696px;left:657px;font-family:"Montserrat",Arial,sans-serif;font-weight:800;font-size:45px;line-height:68px;color:var(--purple);letter-spacing:0;white-space:nowrap}
.cro-title .accent{color:var(--magenta)}
.cro-text{top:1858px;left:661px;width:462px;font-size:13.5px;line-height:26.3px;color:#777;text-align:justify}
.cro-text p{margin-bottom:24px}
.frame-line{position:absolute;background:var(--magenta)}

/* steps */
.step{position:absolute;width:240px;text-align:center}
.step-label{font-family:"Montserrat",Arial,sans-serif;font-weight:700;font-size:20px;color:#222}
.step-text{margin-top:10px;font-size:12.5px;line-height:22px;color:#888}
.step-ring{position:absolute}

/* testimonials */
.scientist-photo{top:3110px;left:729px;width:471px;height:817px;background:linear-gradient(160deg,#eef2f6 0%,#c9d8ea 50%,#6f95c8 100%)}
.kicker{top:3183px;left:45px;font-family:"Montserrat",Arial,sans-serif;font-weight:600;font-size:13.5px;color:#333}
.testimonials-title{top:3200px;left:45px;font-family:"Montserrat",Arial,sans-serif;font-weight:800;font-size:52px;color:var(--magenta)}
.testimonials-text{top:3290px;left:45px;width:598px;font-size:13px;line-height:28.5px;color:#888;text-align:justify}
.quote-box{top:3565px;left:45px;width:825px;height:270px;background:var(--purple)}
.quote-mark{position:absolute;left:38px;top:8px;font-family:"Montserrat",Arial,sans-serif;font-weight:900;font-size:190px;line-height:190px;color:var(--lavender)}
.quote-text{position:absolute;left:157px;top:40px;width:622px;font-size:13.5px;line-height:28.5px;color:#fff}
.quote-author{margin-top:18px}

/* team */
.member{position:absolute;top:4130px;width:285px}
.member-photo{width:100%;height:280px;background:linear-gradient(180deg,#9a8f88 0%,#6e5f58 60%,#3c3330 100%)}
.member-card{position:relative;margin:-12px auto 0;width:255px;height:48px;background:#fff;text-align:center;padding-top:6px}
.member-name{font-family:"Montserrat",Arial,sans-serif;font-weight:700;font-size:17px;color:#333}
.member-role{font-size:10.5px;color:#555;margin-top:2px}
.social-bar{margin:15px auto 0;width:254px;height:47px;display:flex;justify-content:center;align-items:center;gap:22px}
.social-bar.purple{background:var(--purple)}
.social-bar.magenta{background:var(--magenta)}
.social-dot{width:10px;height:10px;border-radius:50%;background:#fff}

/* closing */
.closing{top:4599px;left:0;width:1200px;height:725px;background:linear-gradient(120deg,#d8278e 0%,#9a2cb4 50%,#4b37cc 100%)}
.closing-brand{position:absolute;top:170px;left:0;width:1200px;display:flex;justify-content:center;align-items:center;gap:24px}
.closing-brand .brand-name{font-size:90px}
.closing-brand .brand-square{width:44px;height:44px}
.thank-you{position:absolute;top:450px;width:100%;text-align:center;font-family:"Montserrat",Arial,sans-serif;font-weight:900;font-size:104px;color:#fff;letter-spacing:2px}
</style>
</head>
<body>

<section class="abs hero" role="img" aria-label="Scientist working in a laboratory under a magenta to purple colour wash">
  <div class="brand"><span class="brand-name">lumerova</span><span class="brand-square"></span></div>
</section>

<!-- services -->
<h2 class="abs heading" style="top:862px">OUR SERVICES</h2>
<div class="underline" style="top:931px"></div>

<div class="service" style="left:41px;top:1008px">
  <div class="service-icon purple"><svg width="44" height="44" viewBox="0 0 24 24" fill="none" stroke="#fff" stroke-width="2" stroke-linejoin="round"><path d="M3 10v4h3l7 4V6L6 10z"/><path d="M6 14l1 5h2l-1-5"/><path d="M16 9q2 3 0 6"/></svg></div>
  <div class="service-title">LOREM IPSUM TEXT</div>
  <p class="service-text">Nemo enim ipsam voluptatem quia voluptas sit aspernatur aut odit aut fugit, sed quia consequuntur magni dolores eos qui ratio ne voluptatem sequi nesciun neque</p>
</div>
<div class="service" style="left:646px;top:1008px">
  <div class="service-icon magenta"><svg width="40" height="40" viewBox="0 0 24 24" fill="none" stroke="#fff" stroke-width="2" stroke-linejoin="round"><path d="M6 3h8l4 4v14H6z"/><path d="M14 3v4h4M9 12h6M9 15h6M9 18h6"/></svg></div>
  <div class="service-title">LOREM IPSUM TEXT</div>
  <p class="service-text">Nemo enim ipsam voluptatem quia voluptas sit aspernatur aut odit aut fugit, sed quia consequuntur magni dolores eos qui ratio ne voluptatem sequi nesciun neque</p>
</div>
<div class="service" style="left:41px;top:1198px">
  <div class="service-icon purple"><svg width="44" height="44" viewBox="0 0 24 24" fill="none" stroke="#fff" stroke-width="2"><circle cx="9" cy="13" r="3"/><path d="M9 7v2M9 17v2M3 13h2M13 13h2M5 9l1.5 1.5M13 17l-1.5-1.5M5 17l1.5-1.5M13 9l-1.5 1.5"/><circle cx="18" cy="6" r="2"/><path d="M18 2v1.5M18 8.5V10M14 6h1.5M20.5 6H22"/></svg></div>
  <div class="service-title">LOREM IPSUM TEXT</div>
  <p class="service-text">Nemo enim ipsam voluptatem quia voluptas sit aspernatur aut odit aut fugit, sed quia consequuntur magni dolores eos qui ratio ne voluptatem sequi nesciun neque</p>
</div>
<div class="service" style="left:646px;top:1198px">
  <div class="service-icon magenta"><svg width="40" height="40" viewBox="0 0 24 24" fill="none" stroke="#fff" stroke-width="2" stroke-linejoin="round"><path d="M8 15a6 6 0 1 1 8 0c-1 1-1 2-1 3H9c0-1 0-2-1-3z"/><path d="M9 21h6"/></svg></div>
  <div class="service-title">LOREM IPSUM TEXT</div>
  <p class="service-text">Nemo enim ipsam voluptatem quia voluptas sit aspernatur aut odit aut fugit, sed quia consequuntur magni dolores eos qui ratio ne voluptatem sequi nesciun neque</p>
</div>
<div class="service" style="left:41px;top:1392px">
  <div class="service-icon purple"><svg width="44" height="44" viewBox="0 0 24 24" fill="none" stroke="#fff" stroke-width="2" stroke-linecap="round" stroke-linejoin="round"><path d="M8 7l-5 5 5 5M16 7l5 5-5 5M14 5l-4 14"/></svg></div>
  <div class="service-title">LOREM IPSUM TEXT</div>
  <p class="service-text">Nemo enim ipsam voluptatem quia voluptas sit aspernatur aut odit aut fugit, sed quia consequuntur magni dolores eos qui ratio ne voluptatem sequi nesciun neque</p>
</div>
<div class="service" style="left:646px;top:1392px">
  <div class="service-icon magenta"><svg width="40" height="40" viewBox="0 0 24 24" fill="none" stroke="#fff" stroke-width="2" stroke-linejoin="round"><path d="M21 3L3 10l7 3 3 7z"/><path d="M21 3L10 13"/></svg></div>
  <div class="service-title">LOREM IPSUM TEXT</div>
  <p class="service-text">Nemo enim ipsam voluptatem quia voluptas sit aspernatur aut odit aut fugit, sed quia consequuntur magni dolores eos qui ratio ne voluptatem sequi nesciun neque</p>
</div>

<div class="separator" style="top:1589px"></div>

<!-- clinical research -->
<div class="abs lab-photo" role="img" aria-label="Researcher in safety glasses using a microscope and pipette"></div>
<div class="frame-line" style="left:632px;top:1677px;width:3px;height:146px"></div>
<div class="frame-line" style="left:632px;top:1677px;width:110px;height:3px"></div>
<div class="frame-line" style="left:1144px;top:2200px;width:3px;height:146px"></div>
<div class="frame-line" style="left:998px;top:2343px;width:149px;height:3px"></div>
<h2 class="abs cro-title">CLINICAL <span class="accent">RESEARCH</span><br>ORGANIZATION</h2>
<div class="abs cro-text">
  <p>Sed ut perspiciatis unde omnis iste natus error sit voluptatem accusantium doloremque laudantium, totam rem aperiam, eaque ipsa quae ab illo inventore veritatis et quasi architecto beatae vitae dicta sunt explicabo. Nemo enim ipsam voluptatem quia voluptas sit aspernatur aut odit aut eos qui ratione voluptatem sequi nesciunt.</p>
  <p>Neque porro quisquam est, qui dolorem ipsum quia dolor sit amet, cons ectetur, adipisci velit, sed quia non numquam eius modi tempora incidunt ut labore et dolore magnam aliquam quaerat voluptatem. Ut enim ad m ullam corporis suscipit laboriosam</p>
  <p>But I must explain to you how all this mistaken idea of denouncing pleas ure and praising pain was born and I will give you a complete account of the system, and expound the actual teachings of the great explorer of the truth, the master-builder of human happiness. No one rejects, dislikes, or avoids pleasure itself, because it is pleasure, but because those who do not know how to pursue pleasure rationally encounter consequences that are extremely painful.</p>
</div>

<div class="separator" style="top:2414px"></div>

<!-- how it work -->
<h2 class="abs heading" style="top:2506px">HOW IT WORK</h2>
<div class="underline" style="top:2576px"></div>

<svg width="0" height="0" style="position:absolute"><defs>
  <linearGradient id="ringGrad" x1="0" y1="0" x2="1" y2="1"><stop offset="0" stop-color="#d92a8a"/><stop offset="1" stop-color="#4a33c4"/></linearGradient>
</defs></svg>

<!-- step 1 -->
<svg class="step-ring" style="left:75px;top:2670px" width="180" height="180" viewBox="0 0 180 180" fill="none">
  <circle cx="90" cy="100" r="70" stroke="url(#ringGrad)" stroke-width="2"/>
  <path d="M10 80 A82 82 0 0 1 168 72" stroke="url(#ringGrad)" stroke-width="3"/>
  <path d="M160 66l8 6 2-10" stroke="#4a33c4" stroke-width="3"/>
  <g stroke="#333" stroke-width="3" stroke-linejoin="round"><path d="M70 130h40M80 130v-8h20v8M88 122l14-34 8 4-14 34"/><path d="M104 86l4-8 8 4-4 8"/><path d="M96 112q-14-4-12-20"/></g>
</svg>
<div class="step" style="left:45px;top:2860px"><div class="step-label">STEP 01</div><p class="step-text">Sed ut perspiciatis unde omnis iste natus error sit voluptatem accusantium doloremque laudantium, totam rem ape dicta sunt explicabo.</p></div>

<!-- step 2 -->
<div class="step" style="left:338px;top:2682px"><div class="step-label">STEP 02</div><p class="step-text">Sed ut perspiciatis unde omnis iste natus error sit voluptatem accusantium doloremque laudantium, totam rem ape dicta sunt explicabo.</p></div>
<svg class="step-ring" style="left:368px;top:2812px" width="180" height="190" viewBox="0 0 180 190" fill="none">
  <circle cx="90" cy="90" r="70" stroke="url(#ringGrad)" stroke-width="2"/>
  <path d="M8 110 A82 82 0 0 0 170 110" stroke="url(#ringGrad)" stroke-width="3"/>
  <path d="M162 118l8-8 4 10" stroke="#4a33c4" stroke-width="3"/>
  <g stroke="#333" stroke-width="3"><rect x="56" y="80" width="68" height="26"/><path d="M66 74v24q5 6 10 0V74M86 74v24q5 6 10 0V74M106 74v24q5 6 10 0V74"/></g>
</svg>

<!-- step 3 -->
<svg class="step-ring" style="left:662px;top:2670px" width="180" height="180" viewBox="0 0 180 180" fill="none">
  <circle cx="90" cy="100" r="70" stroke="url(#ringGrad)" stroke-width="2"/>
  <path d="M10 80 A82 82 0 0 1 168 72" stroke="url(#ringGrad)" stroke-width="3"/>
  <path d="M160 66l8 6 2-10" stroke="#4a33c4" stroke-width="3"/>
  <g stroke="#333" stroke-width="3" stroke-linejoin="round"><path d="M106 76l10 10M100 82l10 10-24 24-8 2 2-8z"/><path d="M74 128q-4 6 0 8q4-2 0-8"/></g>
</svg>
<div class="step" style="left:632px;top:2860px"><div class="step-label">STEP 03</div><p class="step-text">Sed ut perspiciatis unde omnis iste natus error sit voluptatem accusantium doloremque laudantium, totam rem ape dicta sunt explicabo.</p></div>

<!-- step 4 -->
<div class="step" style="left:927px;top:2682px"><div class="step-label">STEP 04</div><p class="step-text">Sed ut perspiciatis unde omnis iste natus error sit voluptatem accusantium doloremque laudantium, totam rem ape dicta sunt explicabo.</p></div>
<svg class="step-ring" style="left:957px;top:2812px" width="180" height="190" viewBox="0 0 180 190" fill="none">
  <circle cx="90" cy="90" r="70" stroke="url(#ringGrad)" stroke-width="2"/>
  <path d="M8 110 A82 82 0 0 0 170 110" stroke="url(#ringGrad)" stroke-width="3"/>
  <path d="M162 118l8-8 4 10" stroke="#4a33c4" stroke-width="3"/>
  <g stroke="#333" stroke-width="3" stroke-linejoin="round"><path d="M80 58h20M84 58v28l-20 34h52L96 86V58"/><circle cx="88" cy="108" r="3"/><circle cx="98" cy="100" r="2"/></g>
</svg>

<div class="separator" style="top:3101px"></div>

<!-- testimonials -->
<div class="abs scientist-photo" role="img" aria-label="Scientist in mask and safety glasses handling laboratory glassware"></div>
<p class="abs kicker">SED UT PERSPICIATIS UNDE OMNIS ISTE NATUS ERROR</p>
<h2 class="abs testimonials-title">TESTIMONIALS</h2>
<p class="abs testimonials-text">Nemo enim ipsam voluptatem quia voluptas sit aspernatur aut odit aut fugit, sed quia consequuntur magni dolores eos qui ratione voluptatem sequi nesciunt. Neque porro quisquam est, qui dolorem ipsum quia dolor sit amet, consectetur, adipisci velit, sed quia non numquam eius modi tempora incidunt ut labore et dolore magnam aliquam quaerat voluptatem. Ut enim ad minima veniam, quis nostrum exercitationem ullam corporis suscipit laboriosam, nisi ut aliquid ex ea commodi consequaturSed ut perspiciatis unde omnis iste natus error sit voluptatem accusantium doloremque laudantium, totam rem aperiam, eaque ipsa quae ab illo inventore veritatis et quasi architecto beatae vitae dicta sunt explicabo.</p>
<div class="abs quote-box">
  <div class="quote-mark">&ldquo;</div>
  <div class="quote-text">
    <p>Sed ut perspiciatis unde omnis iste natus error sit voluptatem accusantium doloremque laudantium, totam rem aperiam, eaque ipsa quae ab illo inventore veritatis et quasi architecto beatae vitae dicta sunt explicabo. Nemo enim ipsam voluptatem quia voluptas sit aspernatur aut odit aut fugit, sed quia consequuntur magni dolores eos qui ratione voluptatem sequi nesciunt. Neque porro quisquam est, qui dolorem ipsum quia dolor sit amet....</p>
    <p class="quote-author">-Mara Quell</p>
  </div>
</div>

<div class="separator" style="top:3927px"></div>

<!-- team -->
<h2 class="abs heading" style="top:3996px">OUR TEAM</h2>
<div class="underline" style="top:4068px"></div>

<div class="member" style="left:14px">
  <div class="member-photo" role="img" aria-label="Portrait of team member"></div>
  <div class="member-card"><div class="member-name">DUMMY NAME</div><div class="member-role">Sed ut perspiciatis unde</div></div>
  <div class="social-bar purple"><span class="social-dot"></span><span class="social-dot"></span><span class="social-dot"></span></div>
</div>
<div class="member" style="left:310px">
  <div class="member-photo" role="img" aria-label="Portrait of team member"></div>
  <div class="member-card"><div class="member-name">DUMMY NAME</div><div class="member-role">Sed ut perspiciatis unde</div></div>
  <div class="social-bar magenta"><span class="social-dot"></span><span class="social-dot"></span><span class="social-dot"></span></div>
</div>
<div class="member" style="left:606px">
  <div class="member-photo" role="img" aria-label="Portrait of team member"></div>
  <div class="member-card"><div class="member-name">DUMMY NAME</div><div class="member-role">Sed ut perspiciatis unde</div></div>
  <div class="social-bar purple"><span class="social-dot"></span><span class="social-dot"></span><span class="social-dot"></span></div>
</div>
<div class="member" style="left:902px">
  <div class="member-photo" role="img" aria-label="Portrait of team member"></div>
  <div class="member-card"><div class="member-name">DUMMY NAME</div><div class="member-role">Sed ut perspiciatis unde</div></div>
  <div class="social-bar magenta"><span class="social-dot"></span><span class="social-dot"></span><span class="social-dot"></span></div>
</div>

<!-- closing -->
<section class="abs closing" role="img" aria-label="Laboratory equipment under a magenta to purple colour wash">
  <div class="closing-brand"><span class="brand-name">lumerova</span><span class="brand-square"></span></div>
  <div class="thank-you">THANK YOU</div>
</section>

</body>
</html>
```